Social Media Graphics - Oakline Push REVISED

Create 6-7 individual social media graphics (square size) to encourage folks to join our online course called:

The Harvest Ledger Circle
How to Launch a Multi-Million Business From Scratch
Sign Up Today!

IMPORTANT: Make the largest and most prominent text on the graphic be: How to Launch a Multi-Million Business From Scratch

For the color scheme of the graphics, let's try a blue color palette; make sure the graphics appeal to both men and women

Make sure each graphic contains 1 of the 3 pics attached (crop pic as needed); and make sure one of the graphics is all TEXT only.

Target Market(s)

men and women looking to start a business

Industry/Entity Type

Entrepreneurship

Colors
0054AA
0677BA
7BADD7
CADEEF
E8F1F8

Requirements
Must have
• All the text and use the 3 pics provided; one graphic can be all text; Simple, modern design that's easy to read

```html
<!DOCTYPE html>
<html lang="en">
<head>
<meta charset="utf-8">
<title>The Harvest Ledger Circle – Sign Up Today</title>
<link href="https://fonts.googleapis.com/css2?family=Kaushan+Script&family=Source+Sans+3:wght@800&family=Open+Sans:ital,wght@1,600&family=Oswald:wght@600&display=swap" rel="stylesheet">
<style>
  :root {
    --blue-deep: #0054aa;
    --blue-mid: #0677ba;
    --blue-soft: #7badd7;
    --blue-pale: #cadeef;
    --blue-mist: #e8f1f8;
    --ink: #0a2748;
    --paper: #ffffff;
  }
  html, body {
    margin: 0;
    padding: 0;
    width: 1200px;
    height: 1200px;
    overflow: hidden;
    background: var(--blue-deep);
  }
  .canvas {
    position: relative;
    width: 1200px;
    height: 1200px;
    background: var(--blue-deep);
  }
  .headline-card {
    position: absolute;
    left: 133px;
    top: 100px;
    width: 911px;
    height: 894px;
    background: var(--blue-mist);
    border-radius: 46px;
  }
  .headline {
    margin: 0;
    font-weight: normal;
  }
  .headline-line {
    position: absolute;
    left: 133px;
    width: 911px;
    text-align: center;
    line-height: 1;
    white-space: nowrap;
  }
  .headline-script {
    font-family: "Kaushan Script", cursive;
    color: var(--ink);
  }
  .headline-bold {
    font-family: "Source Sans 3", sans-serif;
    font-weight: 800;
    letter-spacing: -3px;
  }
  .line-launch {
    top: 175px;
    font-size: 105px;
  }
  .line-multi {
    top: 335px;
    font-size: 112px;
    color: var(--blue-mid);
  }
  .line-business {
    top: 480px;
    font-size: 180px;
    color: var(--blue-deep);
  }
  .line-scratch {
    top: 740px;
    font-size: 135px;
  }
  .course-name {
    position: absolute;
    left: 135px;
    top: 1030px;
    margin: 0;
    font-family: "Open Sans", sans-serif;
    font-style: italic;
    font-weight: 600;
    font-size: 36px;
    line-height: 1.3;
    color: var(--paper);
  }
  .signup-button {
    position: absolute;
    left: 670px;
    top: 1033px;
    width: 374px;
    height: 95px;
    border-radius: 14px;
    background: linear-gradient(100deg, var(--blue-soft) 0%, var(--blue-pale) 35%, var(--paper) 75%, var(--blue-pale) 100%);
    display: flex;
    align-items: center;
    justify-content: center;
    font-family: "Oswald", sans-serif;
    font-weight: 600;
    font-size: 50px;
    letter-spacing: 1px;
    color: var(--blue-deep);
    text-transform: uppercase;
  }
  .cursor-icon {
    position: absolute;
    left: 1005px;
    top: 1085px;
    width: 80px;
    height: 80px;
  }
</style>
</head>
<body>
  <main class="canvas">
    <div class="headline-card"></div>
    <h1 class="headline">
      <span class="headline-line headline-script line-launch">How to Launch a</span>
      <span class="headline-line headline-bold line-multi">Multi-Million</span>
      <span class="headline-line headline-bold line-business">Business</span>
      <span class="headline-line headline-script line-scratch">From Scratch</span>
    </h1>
    <p class="course-name">The Harvest Ledger<br>Circle</p>
    <div class="signup-button">Sign Up Today!</div>
    <svg class="cursor-icon" viewBox="0 0 80 80" aria-hidden="true">
      <g stroke="#ffffff" stroke-width="3" stroke-linecap="round">
        <line x1="10" y1="2" x2="10" y2="9"/>
        <line x1="0" y1="12" x2="7" y2="12"/>
        <line x1="3" y1="4" x2="6" y2="7"/>
      </g>
      <path d="M14 14 L14 58 L25 47 L33 66 L42 62 L34 44 L50 44 Z" fill="#0677ba" stroke="#ffffff" stroke-width="3" stroke-linejoin="round"/>
    </svg>
  </main>
</body>
</html>
```